need corporate, modern business card created for Consulting Company

I need a slick business card using elements from my website, as well as, integrating my pixelforge-created logo (see files).

The business card needs to be:
1. Corporate and modern
2. Clean and professional

I've included a PSD with the logo/icon that you can use to create it. Feel free to try a metallic finish on the logo, make it bigger/small, underlay it. Whatever you need to do to make my card stand out.

Try a black background, or white background or gray.

The idea is for my card to be memorable as well as professional and corporate.

Target Market(s)

Corporate business in the US and Canada.

Industry/Entity Type

Business

Contact Information for Business Card

Commerce Advancing Methods
Martin Coles, Senior Partner
office: 1 877 555 0143
mobile: 1 519 555 0172
website: http://www.brightvale.example

Requirements
Must have
• Card-related information
• corporate, yet modern
• clean and professional
• incorporate the icon only
• must have an editable form when complete!
Nice to have
• metallic icon might be cool
• try it with white or black

```html
<!DOCTYPE html>
<html lang="en">
<head>
<meta charset="utf-8">
<title>Brightvale business card</title>
<link rel="stylesheet" href="https://fonts.googleapis.com/css2?family=Open+Sans:wght@400;600;700&display=swap">
<style>
  :root {
    --bg: #e6e4e0;
    --ink: #1e1e1e;
    --band: #1f1f1f;
    --paper: #f4f4f4;
    --blue: #3b7fc2;
    --white: #ffffff;
    --rule: #555555;
  }
  * { box-sizing: border-box; margin: 0; padding: 0; }
  html, body { width: 1200px; height: 864px; overflow: hidden; background: var(--bg); }
  body { font-family: "Open Sans", sans-serif; color: var(--ink); }
  .canvas { position: relative; width: 1200px; height: 864px; }
  .card {
    position: absolute; top: 276px; width: 540px; height: 312px; overflow: hidden;
    box-shadow: 0 6px 18px rgba(0,0,0,0.18);
  }

  /* Front side */
  .card-front { left: 40px; background: var(--paper); }
  .front-top-band { position: absolute; left: 0; top: 0; width: 100%; height: 72px; background: var(--band); }
  .front-brand { position: absolute; left: 32px; top: 20px; display: flex; align-items: center; gap: 10px; }
  .brand-square { width: 22px; height: 22px; background: var(--blue); }
  .front-brand .brand-name { font-size: 28px; font-weight: 700; color: var(--white); letter-spacing: 0.5px; line-height: 1; }
  .holder { position: absolute; left: 0; top: 120px; width: 300px; text-align: center; }
  .holder-name { font-size: 28px; font-weight: 600; letter-spacing: 0.5px; }
  .holder-title { font-size: 13px; margin-top: 2px; }
  .divider { position: absolute; left: 306px; top: 98px; width: 1px; height: 120px; background: var(--rule); }
  .contact-list { position: absolute; left: 326px; top: 96px; width: 190px; list-style: none; }
  .contact-list li {
    display: flex; align-items: center; gap: 12px; height: 30px;
    border-bottom: 1px solid var(--rule); font-size: 13px;
  }
  .contact-list svg { width: 14px; height: 14px; flex: none; }
  .front-bottom-band { position: absolute; left: 0; bottom: 0; width: 100%; height: 76px; background: var(--band); }
  .address { position: absolute; left: 28px; top: 18px; font-size: 13.5px; color: var(--white); letter-spacing: 0.2px; }

  /* Back side */
  .card-back { left: 620px; background: var(--blue); }
  .back-stripe { position: absolute; left: 34px; top: 0; width: 86px; height: 100%; background: var(--paper); }
  .back-corner-top { position: absolute; right: 0; top: 70px; width: 150px; height: 30px; background: var(--paper); }
  .back-corner-bottom { position: absolute; right: 0; bottom: 0; width: 170px; height: 36px; background: var(--paper); }
  .back-brand { position: absolute; left: 170px; top: 116px; }
  .back-brand .brand-row { display: flex; align-items: center; gap: 12px; }
  .back-brand .brand-square { width: 30px; height: 30px; background: var(--ink); }
  .back-brand .brand-name { font-size: 44px; font-weight: 700; color: var(--ink); line-height: 1; letter-spacing: 0.5px; }
  .tagline { font-size: 14px; color: var(--white); margin-top: 8px; letter-spacing: 0.3px; }
</style>
</head>
<body>
<main class="canvas">
  <section class="card card-front" aria-label="Card front">
    <div class="front-top-band">
      <div class="front-brand">
        <span class="brand-square"></span>
        <span class="brand-name">brightvale</span>
      </div>
    </div>
    <div class="holder">
      <p class="holder-name">Martin Coles</p>
      <p class="holder-title">Senior Partner</p>
    </div>
    <div class="divider"></div>
    <ul class="contact-list">
      <li>
        <svg viewBox="0 0 16 16"><path d="M3 1.5l3 3-1.6 1.8c.9 2 2.3 3.4 4.3 4.3L10.5 9l3 3-2 2C6.5 13.6 2.4 9.5 1 3.5z" fill="#1e1e1e"/></svg>
        <span>1 877 555 0143</span>
      </li>
      <li>
        <svg viewBox="0 0 16 16"><rect x="4.5" y="1" width="7" height="14" rx="1.2" fill="none" stroke="#1e1e1e" stroke-width="1.4"/><circle cx="8" cy="12.6" r="0.9" fill="#1e1e1e"/></svg>
        <span>1 519 555 0172</span>
      </li>
      <li>
        <svg viewBox="0 0 16 16"><rect x="1.5" y="2.5" width="13" height="9" fill="none" stroke="#1e1e1e" stroke-width="1.4"/><path d="M6 14.5h4M8 11.5v3" stroke="#1e1e1e" stroke-width="1.4"/></svg>
        <span>www.brightvale.example</span>
      </li>
      <li>
        <svg viewBox="0 0 16 16"><rect x="1" y="3.5" width="14" height="9" fill="#1e1e1e"/><path d="M1.5 4l6.5 5 6.5-5" fill="none" stroke="#f4f4f4" stroke-width="1.2"/></svg>
        <span>info@brightvale.example</span>
      </li>
    </ul>
    <div class="front-bottom-band">
      <p class="address">48 Harbour Lane West, Suite 1410, Toronto, Ontario, M5J 2K7</p>
    </div>
  </section>

  <section class="card card-back" aria-label="Card back">
    <div class="back-stripe"></div>
    <div class="back-corner-top"></div>
    <div class="back-corner-bottom"></div>
    <div class="back-brand">
      <div class="brand-row">
        <span class="brand-square"></span>
        <span class="brand-name">brightvale</span>
      </div>
      <p class="tagline">Commerce Advancing Methods</p>
    </div>
  </section>
</main>
</body>
</html>
```